Verodex business card

Business card for sustainable investment company called "Verodex". Verodex is an exchange platform selling carbon credits between buyers and sellers. Carbon Credits are an environmental commodity for reducing global carbon emissions.

the card should obviously have our logo and the theme should be sustainability/environment mixed with a trading platform.

Contact Information for Business Card

Logo, Name, Title, Phone, Email

Colors
0054AA
0677BA
7BADD7
CADEEF
E8F1F8
0094D4
00A9DD
6FCCEA
C7EBF8
E9F6FB
00AB8E
00BBA5
67D7C9
C6EFE9
E9F9F6
59FF00
82FF00
B8FF75
E3FFCB
F4FFEA

```html
<!DOCTYPE html>
<html lang="en">
<head>
<meta charset="utf-8">
<title>Verodex Business Card</title>
<link rel="stylesheet" href="https://fonts.googleapis.com/css2?family=Raleway:wght@700&family=Montserrat:wght@500&family=Pinyon+Script&display=swap">
<style>
  :root {
    --page-bg: #d3d4d6;
    --navy: #172b53;
    --navy-ink: #1a2d58;
    --white: #ffffff;
    --sky: #6fccea;
    --azure: #0677ba;
    --name-start: #6fccea;
    --name-end: #4a86cc;
    --rule: #4fa6d8;
  }
  * { margin: 0; padding: 0; box-sizing: border-box; }
  html, body {
    width: 900px;
    height: 1200px;
    overflow: hidden;
    background: var(--page-bg);
  }
  .canvas {
    position: relative;
    width: 900px;
    height: 1200px;
  }
  .card {
    position: absolute;
    left: 90px;
    width: 720px;
  }
  .card-front {
    top: 152px;
    height: 407px;
    background: var(--navy);
  }
  .card-back {
    top: 615px;
    height: 433px;
    background: var(--white);
  }
  .wordmark {
    position: absolute;
    display: flex;
    align-items: center;
    font-family: "Raleway", sans-serif;
    font-weight: 700;
    line-height: 1;
    white-space: nowrap;
  }
  .card-front .wordmark {
    left: 50%;
    top: 50%;
    transform: translate(-50%, -50%);
    gap: 16px;
    font-size: 52px;
    color: var(--white);
  }
  .mark-square {
    display: block;
    width: 34px;
    height: 34px;
    background: var(--sky);
  }
  .card-back .mark-square {
    position: absolute;
    left: 50%;
    top: 64px;
    width: 48px;
    height: 48px;
    transform: translateX(-50%);
    background: var(--azure);
  }
  .card-back .wordmark {
    left: 0;
    right: 0;
    top: 136px;
    justify-content: center;
    font-size: 54px;
    color: var(--navy-ink);
  }
  .person-name {
    position: absolute;
    left: 0;
    right: 0;
    top: 252px;
    text-align: center;
    font-family: "Raleway", sans-serif;
    font-weight: 700;
    font-size: 29px;
    letter-spacing: 0.02em;
    background: linear-gradient(90deg, var(--name-start), var(--name-end));
    -webkit-background-clip: text;
    background-clip: text;
    color: transparent;
    width: max-content;
    margin: 0 auto;
  }
  .person-title {
    position: absolute;
    left: 0;
    right: 0;
    top: 284px;
    text-align: center;
    font-family: "Pinyon Script", cursive;
    font-size: 20px;
    color: var(--navy-ink);
  }
  .contact {
    position: absolute;
    left: 0;
    right: 0;
    text-align: center;
    font-family: "Montserrat", sans-serif;
    font-weight: 500;
    font-size: 17px;
    letter-spacing: 0.22em;
    color: var(--navy-ink);
    white-space: nowrap;
  }
  .contact-line { top: 328px; }
  .contact-email { top: 366px; font-size: 16px; }
  .divider {
    display: inline-block;
    width: 2px;
    height: 22px;
    margin: 0 14px 0 6px;
    vertical-align: -5px;
    background: var(--rule);
  }
</style>
</head>
<body>
  <main class="canvas">
    <section class="card card-front" aria-label="Card front">
      <div class="wordmark">
        <span class="mark-square" aria-hidden="true"></span>
        <span>Verodex</span>
      </div>
    </section>

    <section class="card card-back" aria-label="Card back">
      <span class="mark-square" aria-hidden="true"></span>
      <div class="wordmark">Verodex</div>
      <h1 class="person-name">DANIEL REYES</h1>
      <p class="person-title">Founder</p>
      <p class="contact contact-line">WWW.VERODEX.COM<span class="divider" aria-hidden="true"></span>303-555-0148</p>
      <p class="contact contact-email">INFO@VERODEX.COM</p>
    </section>
  </main>
</body>
</html>
```